Business Card for Fashion House

We need a business card design for our personalize fashion service for our customers. the business card should reflect reliability, luxury and creativity.
The brand Gravetto is extracted from "Graceful Velvetto"; Gravetto provides fashion designs sprinkled with luxury and style tailored for our elite clients character profile.
Gravetto is created for those who embody class and elegance with a passion for style.
Target Market(s)
Affluent Customers
Industry/Entity Type
Fashion
Contact Information for Business Card
Samira Haddadin
Fashion Designer
Telephone: +971 4 555 0192
Mobile +971 50 555 0147
Emal info@gravetto-example.com
Website www.gravetto-example.com
Social Media Youtube g+ Facebook Instagram Pin /gravetto
Font styles to use
Other font styles liked:
- Audrey provided
Look and feel
Each slider illustrates characteristics of the customer's brand and the style your logo design should communicate.

```html
<!DOCTYPE html>
<html lang="en">
<head>
<meta charset="utf-8">
<title>Gravetto — Business Card</title>
<link rel="stylesheet" href="https://fonts.googleapis.com/css2?family=Marcellus&family=Roboto:wght@400&display=swap">
<style>
  :root {
    --backdrop: #3a3a3c;
    --card-black: #1d1d20;
    --silver-light: #f2f2f2;
    --silver-mid: #c9c9cb;
    --silver-dark: #8e8e92;
    --text-white: #f4f4f4;
    --text-dark: #1b1b1d;
    --social-dot: #6b6b70;
  }
  * { margin: 0; padding: 0; box-sizing: border-box; }
  html, body { width: 799px; height: 1200px; overflow: hidden; }
  body {
    background: var(--backdrop);
    position: relative;
    font-family: "Roboto", sans-serif;
  }
  .card {
    position: absolute;
    left: 90px;
    width: 620px;
    height: 354px;
    background: var(--card-black);
    border-radius: 4px;
    overflow: hidden;
    box-shadow: 0 10px 30px rgba(0,0,0,0.45);
  }
  .card--front { top: 150px; }
  .card--back { top: 700px; }

  .brand {
    position: absolute;
    display: flex;
    align-items: center;
    gap: 14px;
    font-family: "Marcellus", serif;
    color: var(--silver-mid);
    letter-spacing: 0.32em;
  }
  .brand__dot {
    border: 2px solid var(--silver-mid);
    border-radius: 50%;
  }
  .card--front .brand {
    left: 50%; top: 50%;
    transform: translate(-50%, -50%);
    font-size: 34px;
  }
  .card--front .brand__dot { width: 22px; height: 22px; }

  .card--back .brand {
    right: 38px; top: 150px;
    font-size: 20px;
    gap: 10px;
  }
  .card--back .brand__dot { width: 14px; height: 14px; }

  .wave { position: absolute; left: 0; top: 0; width: 620px; height: 354px; }

  .holder {
    position: absolute; left: 70px; top: 36px;
    color: var(--text-white);
  }
  .holder__name { font-family: "Marcellus", serif; font-size: 23px; font-weight: 400; }
  .holder__title { font-size: 11px; margin-top: 2px; }

  .contacts {
    position: absolute; left: 44px; top: 110px;
    list-style: none;
    color: var(--text-white);
    font-size: 13px;
  }
  .contacts li { display: flex; align-items: center; gap: 10px; height: 17px; }
  .contacts svg { width: 12px; height: 12px; flex: none; }

  .social {
    position: absolute; right: 44px; top: 290px;
    display: flex; flex-direction: column; align-items: center;
  }
  .social__dots { display: flex; gap: 4px; }
  .social__dot { width: 14px; height: 14px; border-radius: 50%; background: var(--social-dot); }
  .social__handle { font-size: 16px; color: var(--text-dark); margin-top: 4px; }
</style>
</head>
<body>

<section class="card card--front">
  <div class="brand"><span class="brand__dot"></span>GRAVETTO</div>
</section>

<section class="card card--back">
  <svg class="wave" viewBox="0 0 620 354" aria-hidden="true">
    <defs>
      <linearGradient id="silver" x1="0" y1="0" x2="1" y2="1">
        <stop offset="0" stop-color="#9a9a9e"/>
        <stop offset="0.45" stop-color="#f2f2f2"/>
        <stop offset="0.75" stop-color="#c6c6c8"/>
        <stop offset="1" stop-color="#ececec"/>
      </linearGradient>
    </defs>
    <path d="M0,188 C150,150 320,230 620,236 L620,244 C320,240 150,172 0,206 Z" fill="url(#silver)"/>
    <path d="M0,222 C150,196 330,262 620,258 L620,354 L0,354 Z" fill="url(#silver)"/>
  </svg>

  <header class="holder">
    <h1 class="holder__name">Samira Haddadin</h1>
    <p class="holder__title">Fashion Designer</p>
  </header>

  <ul class="contacts">
    <li>
      <svg viewBox="0 0 12 12"><circle cx="6" cy="6" r="5.3" fill="none" stroke="#f4f4f4" stroke-width="1"/><path d="M4 3.5 L5 3.5 L5.5 5 L4.8 5.5 Q5.5 7 6.7 7.4 L7.2 6.7 L8.6 7.2 L8.6 8.2 Q5 8.5 4 3.5Z" fill="#f4f4f4"/></svg>
      +971 4 555 0192
    </li>
    <li>
      <svg viewBox="0 0 12 12"><rect x="3.5" y="1" width="5" height="10" rx="1" fill="none" stroke="#f4f4f4" stroke-width="1"/><circle cx="6" cy="9.3" r="0.6" fill="#f4f4f4"/></svg>
      +971 50 555 0147
    </li>
    <li>
      <svg viewBox="0 0 12 12"><rect x="1" y="2.5" width="10" height="7" fill="none" stroke="#f4f4f4" stroke-width="1"/><path d="M1 2.5 L6 6.5 L11 2.5" fill="none" stroke="#f4f4f4" stroke-width="1"/></svg>
      info@gravetto-example.com
    </li>
    <li>
      <svg viewBox="0 0 12 12"><circle cx="6" cy="6" r="5" fill="none" stroke="#f4f4f4" stroke-width="1"/><ellipse cx="6" cy="6" rx="2.2" ry="5" fill="none" stroke="#f4f4f4" stroke-width="0.8"/><path d="M1 6 H11" stroke="#f4f4f4" stroke-width="0.8"/></svg>
      www.gravetto-example.com
    </li>
  </ul>

  <div class="brand"><span class="brand__dot"></span>GRAVETTO</div>

  <div class="social">
    <div class="social__dots">
      <span class="social__dot"></span><span class="social__dot"></span><span class="social__dot"></span><span class="social__dot"></span><span class="social__dot"></span>
    </div>
    <span class="social__handle">/gravetto</span>
  </div>
</section>

</body>
</html>
```